Stonebridge Building and Projects business cards

A business card with watermark background (construction work)

Company logo attached

Home improvement projects
House renovations
Bathroom and kitchen renovations
House extensions
New builds and granny flats

Director Omar Haddani
(Phone number)
omar@sbpbuilding.com.au
(Instagram logo) sbp_building

```html
<!DOCTYPE html>
<html lang="en">
<head>
<meta charset="utf-8">
<title>Stonebridge Building and Projects – Business Cards</title>
<link rel="stylesheet" href="https://fonts.googleapis.com/css2?family=Montserrat:wght@600&family=Roboto:wght@400;500;700&display=swap">
<style>
  :root {
    --bg: #2b2b2d;
    --card: #f4f5f6;
    --blue: #1a78c2;
    --blue-dark: #145f9c;
    --grey: #3d4046;
    --ink: #2f3237;
    --muted: #5b6068;
    --watermark: #e6e8eb;
  }
  * { box-sizing: border-box; margin: 0; padding: 0; }
  html, body { width: 1200px; height: 1050px; overflow: hidden; }
  body {
    background: var(--bg);
    font-family: "Roboto", Arial, sans-serif;
    position: relative;
  }
  .card {
    position: absolute;
    width: 490px;
    height: 280px;
    background: var(--card);
    border-radius: 18px;
    overflow: hidden;
    box-shadow: 0 14px 30px rgba(0,0,0,.45);
  }
  .card--services { left: 110px; top: 170px; }
  .card--contact { left: 600px; top: 590px; }

  /* services card */
  .watermark {
    position: absolute;
    left: 120px; top: 0;
    width: 230px; height: 280px;
    background: linear-gradient(160deg, var(--watermark), rgba(230,232,235,0) 85%);
  }
  .brand {
    position: absolute;
    font-family: "Montserrat", Arial, sans-serif;
    font-weight: 600;
    color: var(--blue);
    line-height: 1.15;
    display: flex;
    align-items: flex-start;
    gap: 8px;
  }
  .brand__mark {
    width: 12px; height: 12px;
    background: var(--blue);
    margin-top: 5px;
    flex: none;
  }
  .card--services .brand { left: 28px; top: 120px; width: 200px; font-size: 19px; }
  .services {
    position: absolute;
    left: 262px; top: 38px;
    list-style: none;
    font-size: 13.5px;
    color: var(--ink);
    line-height: 1.55;
  }
  .services li { position: relative; padding-left: 20px; }
  .services li::before {
    content: "";
    position: absolute;
    left: 0; top: 7px;
    width: 7px; height: 7px;
    background: var(--blue);
  }
  .band {
    position: absolute;
    right: 0; bottom: 0;
    width: 260px; height: 62px;
    background: var(--blue);
    border-top-left-radius: 16px;
    color: #fff;
    font-size: 13px;
    display: flex;
    align-items: center;
    padding-left: 40px;
    gap: 9px;
  }
  .band .dot { width: 12px; height: 12px; border: 1.6px solid #fff; border-radius: 50%; }
  .edge {
    position: absolute;
    left: 0; bottom: 0;
    width: 240px; height: 8px;
    background: var(--grey);
  }

  /* contact card */
  .card--contact .brand { left: 100px; top: 34px; width: 250px; font-size: 21px; }
  .wave { position: absolute; inset: 0; }
  .person {
    position: absolute;
    right: 24px; top: 124px;
    text-align: right;
    color: #fff;
  }
  .person__name { font-size: 19px; font-weight: 700; }
  .person__role { font-size: 12.5px; margin-top: 2px; }
  .contacts {
    position: absolute;
    left: 30px; top: 140px;
    list-style: none;
    font-size: 13.5px;
    color: var(--ink);
    line-height: 1.6;
  }
  .contacts li { display: flex; align-items: center; gap: 9px; }
  .contacts svg { width: 13px; height: 13px; flex: none; }
</style>
</head>
<body>

<section class="card card--services">
  <div class="watermark" role="img" aria-label="Faint construction work photo watermark"></div>
  <div class="brand"><span class="brand__mark"></span><span>Stonebridge Building and Projects</span></div>
  <ul class="services">
    <li>Home improvement projects</li>
    <li>House renovations</li>
    <li>Bathroom and kitchen<br>renovations</li>
    <li>House extensions</li>
    <li>New builds and granny flats</li>
  </ul>
  <div class="edge"></div>
  <div class="band"><span class="dot"></span>sbp_building</div>
</section>

<section class="card card--contact">
  <svg class="wave" viewBox="0 0 490 280" preserveAspectRatio="none" aria-hidden="true">
    <path d="M0 262 C190 266 290 220 330 140 C365 72 420 56 490 58 L490 280 L0 280 Z" fill="var(--blue)"/>
    <path d="M0 240 C180 244 275 200 315 128 C352 58 415 38 490 42 L490 52 C420 48 368 64 332 132 C290 212 190 254 0 250 Z" fill="var(--grey)"/>
  </svg>
  <div class="brand"><span class="brand__mark"></span><span>Stonebridge Building and Projects</span></div>
  <div class="person">
    <div class="person__name">Omar Haddani</div>
    <div class="person__role">Managing Director</div>
  </div>
  <ul class="contacts">
    <li><svg viewBox="0 0 16 16"><circle cx="8" cy="8" r="7" fill="none" stroke="var(--blue)" stroke-width="1.5"/><path d="M5.5 4.5l1.5 1.5-1 1c.6 1.2 1.6 2.2 2.8 2.8l1-1 1.5 1.5-1 1.2C7.5 11.3 4.7 8.5 4.5 5.5z" fill="var(--blue)"/></svg>0400 318 572</li>
    <li><svg viewBox="0 0 16 16"><rect x="1.5" y="3.5" width="13" height="9" fill="none" stroke="var(--blue)" stroke-width="1.5"/><path d="M1.5 3.5L8 9l6.5-5.5" fill="none" stroke="var(--blue)" stroke-width="1.5"/></svg>omar@sbpbuilding.com.au</li>
    <li><svg viewBox="0 0 16 16"><circle cx="8" cy="8" r="6.5" fill="none" stroke="var(--blue)" stroke-width="1.5"/><path d="M1.5 8h13M8 1.5c-3 3.5-3 9.5 0 13M8 1.5c3 3.5 3 9.5 0 13" fill="none" stroke="var(--blue)" stroke-width="1.2"/></svg>www.sbpbuilding.com.au</li>
    <li><svg viewBox="0 0 16 16"><circle cx="8" cy="8" r="6.5" fill="none" stroke="var(--blue)" stroke-width="1.5"/></svg>sbp_building</li>
  </ul>
</section>

</body>
</html>
```